Brightbay Orthodontics business card design

Need a business card design that reflects our re-branding (orthodontic office - braces) and a new partnership with a pediatric dental office. We would like to include "for adults and children" on the card as well so adults know they are welcome to get their braces here as well. Office design is modern and would like business card to reflect a modern type look. Here's the text we would like to be included on the card:

Darren Wolcott, DDS, MSD
5214 West Linden Avenue, Suite 204
Harwick, OR 76991
555-418-2637
www.brightbayortho.example
info@brightbayortho.example

Can we add the following to the existing designs? Darren Wolcott, DDS, MSD 5214 West Linden Avenue, Suite 204 Harwick, OR 76991 555-418-2637

Does anyone have any more vertical designs available? Thanks!

Dental

```html
<!DOCTYPE html>
<html lang="en">
<head>
<meta charset="utf-8">
<title>Brightbay Orthodontics – Business Card</title>
<link rel="stylesheet" href="https://fonts.googleapis.com/css2?family=Lato:wght@400;700;900&family=Montserrat:wght@400&display=swap">
<style>
  :root {
    --backdrop: #2b2b2b;
    --brand-blue: #1670b8;
    --brand-blue-deep: #0f5c9c;
    --paper: #f4f4f4;
    --ink: #1e1e1e;
    --white: #ffffff;
    --accent-yellow: #f2e400;
    --accent-magenta: #e0157f;
    --accent-green: #79b530;
    --accent-orange: #ea8a1e;
    --accent-black: #151515;
  }
  * { box-sizing: border-box; margin: 0; padding: 0; }
  html, body {
    width: 1200px; height: 768px; overflow: hidden;
    background: var(--backdrop);
    font-family: "Lato", sans-serif;
  }
  .canvas { position: relative; width: 1200px; height: 768px; }
  .business-card {
    position: absolute; left: 420px; top: 69px;
    width: 360px; height: 630px;
    border-radius: 22px; overflow: hidden;
    background: var(--paper);
    box-shadow: 0 14px 40px rgba(0,0,0,.45);
  }
  .card-shapes { position: absolute; inset: 0; }
  .doctor {
    position: absolute; top: 22px; left: 0; right: 0;
    text-align: center; color: var(--white);
  }
  .doctor-name {
    font-family: "Montserrat", sans-serif; font-weight: 400;
    font-size: 22px; letter-spacing: 1.5px;
  }
  .doctor-credentials {
    font-size: 13px; letter-spacing: 1px; margin-top: 2px;
    padding-left: 70px;
  }
  .brand {
    position: absolute; top: 160px; left: 0; right: 0;
    display: flex; flex-direction: column; align-items: center;
  }
  .brand-lockup { display: flex; align-items: center; gap: 14px; }
  .brand-mark {
    width: 52px; height: 52px; border-radius: 50%;
    background: var(--brand-blue); flex: none;
  }
  .brand-name {
    font-weight: 900; font-size: 33px; line-height: 1.05;
    color: var(--ink);
  }
  .brand-tagline {
    margin-top: 14px; font-size: 15px; letter-spacing: 2.4px;
    color: var(--ink);
  }
  .contact-list {
    position: absolute; top: 400px; left: 38px; right: 20px;
    list-style: none; color: var(--white);
  }
  .contact-item {
    display: flex; align-items: flex-start; gap: 16px;
    font-size: 16px; line-height: 1.45; margin-bottom: 22px;
  }
  .contact-icon { width: 26px; height: 26px; flex: none; }
</style>
</head>
<body>
<main class="canvas">
  <article class="business-card">
    <svg class="card-shapes" width="360" height="630" viewBox="0 0 360 630" aria-hidden="true">
      <!-- header band -->
      <rect x="0" y="0" width="360" height="86" fill="var(--brand-blue)"/>
      <g class="accent-strip">
        <rect x="0" y="86" width="72" height="5" fill="var(--accent-yellow)"/>
        <rect x="72" y="86" width="72" height="5" fill="var(--accent-magenta)"/>
        <rect x="144" y="86" width="72" height="5" fill="var(--accent-green)"/>
        <rect x="216" y="86" width="72" height="5" fill="var(--accent-orange)"/>
        <rect x="288" y="86" width="72" height="5" fill="var(--accent-black)"/>
      </g>
      <!-- contact panel -->
      <g class="accent-strip">
        <rect x="0" y="345" width="72" height="5" fill="var(--accent-yellow)"/>
        <rect x="72" y="345" width="72" height="5" fill="var(--accent-magenta)"/>
        <rect x="144" y="345" width="72" height="5" fill="var(--accent-green)"/>
        <rect x="216" y="345" width="72" height="5" fill="var(--accent-orange)"/>
        <rect x="288" y="345" width="72" height="5" fill="var(--accent-black)"/>
      </g>
      <rect x="0" y="350" width="360" height="280" fill="var(--brand-blue)"/>
      <path d="M0 630 V520 Q180 470 360 500 V630 Z" fill="var(--brand-blue-deep)" opacity=".35"/>
    </svg>

    <header class="doctor">
      <p class="doctor-name">Darren Wolcott</p>
      <p class="doctor-credentials">DDS, MSD</p>
    </header>

    <section class="brand">
      <div class="brand-lockup">
        <span class="brand-mark" aria-hidden="true"></span>
        <h1 class="brand-name">Brightbay<br>Orthodontics</h1>
      </div>
      <p class="brand-tagline">FOR ADULTS &amp; CHILDREN</p>
    </section>

    <ul class="contact-list">
      <li class="contact-item">
        <svg class="contact-icon" viewBox="0 0 26 26" aria-hidden="true">
          <path d="M3 9 Q13 2 23 9 L21 12 L17 10 V8 H9 V10 L5 12 Z" fill="var(--white)"/>
          <rect x="6" y="13" width="14" height="9" rx="2" fill="var(--white)"/>
        </svg>
        <span>555-418-2637</span>
      </li>
      <li class="contact-item">
        <svg class="contact-icon" viewBox="0 0 26 26" aria-hidden="true">
          <circle cx="13" cy="13" r="11" fill="none" stroke="var(--white)" stroke-width="2.5"/>
          <path d="M2 13 H24 M13 2 Q6 13 13 24 M13 2 Q20 13 13 24" fill="none" stroke="var(--white)" stroke-width="1.8"/>
        </svg>
        <span>www.brightbayortho.example</span>
      </li>
      <li class="contact-item">
        <svg class="contact-icon" viewBox="0 0 26 26" aria-hidden="true">
          <rect x="2" y="6" width="22" height="15" rx="1.5" fill="var(--white)"/>
          <path d="M2.5 7 L13 15 L23.5 7" fill="none" stroke="var(--brand-blue)" stroke-width="1.6"/>
        </svg>
        <span>info@brightbayortho.example</span>
      </li>
      <li class="contact-item">
        <svg class="contact-icon" viewBox="0 0 26 26" aria-hidden="true">
          <path d="M13 2 A8 8 0 0 1 21 10 C21 16 13 24 13 24 C13 24 5 16 5 10 A8 8 0 0 1 13 2 Z" fill="var(--white)"/>
          <circle cx="13" cy="10" r="3" fill="var(--brand-blue)"/>
        </svg>
        <span>5214 West Linden Avenue, Suite 204<br>Harwick, OR 76991</span>
      </li>
    </ul>
  </article>
</main>
</body>
</html>
```